BrivoNest Learning App for Children with Dyslexia

Project Description:

We are seeking a talented UI/UX designer to create engaging and intuitive designs for Brivonest, an innovative educational app designed to help children learn letters and words through a multisensory learning approach. The app aims to be particularly helpful for children with dyslexia, providing a supportive and interactive learning environment.

Key App Features & Design Requirements:

Account Creation Screen: Design a welcoming and straightforward sign-up page that allows users to register with their email or continue with Quarnix. The design should be clean, focusing on user-friendliness and accessibility, adhering to our terms of service and privacy policy.

Main Screen Design: The main screen should allocate at least 4/6 of its height to the interactive drawing area. It needs to display word prompts in both correct and scrambled orders and include options to "Show all Words," "Play all words," and a search function. The interface should be vibrant, engaging, and easy to navigate for children.

Profile Section: Create a user-friendly profile page that allows users to edit their profile image, name, username, email, links, and bio. The design should be clean and encourage user engagement.

BrivoTally Page: This section will display the user's learning progress, including rankings, a learning curve, and recently learned words. It should visually represent progress in a motivating and understandable way, suitable for a younger audience.

Visual and Auditory Feedback Implementation: Incorporate elements that support visual and auditory feedback, using dyslexia-friendly formats. This includes choosing appropriate colors, fonts, and auditory cues.

Accessibility and Customization Settings: Designs should include settings for adjusting visual contrast, font size, and the word list to accommodate individual preferences and needs.

Feel free to add more interactions and/or pages.

Design preferences:

Color Scheme: Use a bright, inviting color palette that stimulates learning and engagement without overwhelming the users.
Font Selection: Opt for fonts that are readable and accessible, particularly for users with dyslexia.
Icons and Graphics: Design custom icons and graphics that are cohesive with the app's theme and purpose. Illustrations should be simple, relatable, and supportive of the learning process.

Target Market(s)

Educational

Industry/Entity Type

Educational

Colors
0054AA
0677BA
7BADD7
CADEEF
E8F1F8
0094D4
00A9DD
6FCCEA
C7EBF8
E9F6FB

Requirements
Must have
• Educational app, a writing area, scoring and account management
Nice to have
• Statistics, Ranking Page, Settings and some nice visual features

```html
<!DOCTYPE html>
<html lang="en">
<head>
<meta charset="utf-8">
<title>Brivonest – App Screens</title>
<link href="https://fonts.googleapis.com/css2?family=Poppins:wght@400;500;600;700&display=swap" rel="stylesheet">
<style>
:root{
  --navy:#0054AA;
  --blue:#0677BA;
  --soft-blue:#7BADD7;
  --pale-blue:#CADEEF;
  --mist:#E8F1F8;
  --sky:#0094D4;
  --cyan:#00A9DD;
  --light-cyan:#6FCCEA;
  --ice:#C7EBF8;
  --frost:#E9F6FB;
  --page:#e3e3e3;
  --ink:#0d2a4d;
  --label:#6f93bf;
}
*{box-sizing:border-box;margin:0;padding:0}
html,body{width:1200px;height:706px;overflow:hidden}
body{background:var(--page);font-family:'Poppins',sans-serif;position:relative}
.screen{position:absolute;top:79px;width:230px;height:476px;background:#fff;border-radius:28px;overflow:hidden;box-shadow:0 6px 18px rgba(40,70,110,.18)}
.signup{left:59px}
.main{left:337px}
.profile{left:625px}
.stats{left:898px}
.t{position:absolute;transform:translateY(-50%);white-space:nowrap;line-height:1.2}
.tc{position:absolute;transform:translate(-50%,-50%);white-space:nowrap;line-height:1.2}
.sky{position:absolute;left:0;right:0;background:linear-gradient(180deg,var(--ice) 0%,var(--frost) 70%,#fff 100%)}
.topbar{position:absolute;left:0;right:0;top:0;height:38px;background:#fff;z-index:2}
.burger{position:absolute;left:15px;top:16px;width:14px;height:10px;border-top:1.5px solid var(--navy);border-bottom:1.5px solid var(--navy)}
.burger::after{content:"";position:absolute;left:0;right:0;top:3px;border-top:1.5px solid var(--navy)}
.screen-title{font-size:14px;font-weight:700;color:var(--navy)}
/* sign up */
.brand{font-size:33px;font-weight:700;color:var(--navy);letter-spacing:-.5px}
.tagline{font-size:12.5px;color:var(--sky)}
.heading{font-size:15px;font-weight:600;color:var(--navy)}
.subhead{font-size:9px;color:var(--sky)}
.field{position:absolute;left:26px;top:239px;width:181px;height:31px;border:1px solid var(--soft-blue);font-size:9.5px;color:var(--navy);padding-left:12px;line-height:29px}
.btn-primary{position:absolute;background:linear-gradient(90deg,var(--blue),var(--navy));color:#fff;font-weight:600;font-size:10px;display:flex;align-items:center;justify-content:center}
.divider-text{font-size:8px;color:var(--navy)}
.rule{position:absolute;height:1px;background:var(--soft-blue)}
.alt-login{position:absolute;left:26px;top:343px;width:181px;height:30px;background:#dce8f4;display:flex;align-items:center;justify-content:center;gap:6px;font-size:11px;color:var(--navy)}
.alt-login .dot{width:10px;height:10px;border-radius:50%;background:var(--sky)}
.legal{font-size:7px;color:#6f7c8c}
.legal-strong{font-size:7px;color:#1b2736}
/* main */
.points{font-size:7.5px;color:var(--sky)}
.illustration{position:absolute;left:25px;top:66px;width:183px;height:160px;border-radius:60px 60px 20px 20px;background:radial-gradient(ellipse at 50% 45%,#f4f8fd 0%,#dcebf7 60%,#bfe3f1 100%)}
.toggle{position:absolute;left:25px;top:254px;width:189px;height:29px;border-radius:15px;background:var(--mist);border:1px solid var(--pale-blue)}
.toggle .off{position:absolute;left:17px;top:50%;transform:translateY(-50%);font-size:8px;color:var(--soft-blue)}
.toggle .on{position:absolute;right:4px;top:3px;width:88px;height:21px;border-radius:11px;background:#fff;font-size:8px;color:var(--navy);display:flex;align-items:center;justify-content:center}
.word{position:absolute;width:63px;height:21px;background:var(--sky);color:#fff;font-weight:600;font-size:9px;display:flex;align-items:center;justify-content:center}
.results{left:22px;top:369px;width:181px;height:31px;border-radius:16px}
/* profile */
.ring{position:absolute;border-radius:50%;transform:translate(-50%,-50%)}
.avatar{background:radial-gradient(circle at 50% 40%,#b58a6c,#5a3d2b 70%,#2d231c)}
.label{font-size:8.5px;color:var(--label)}
.value{font-size:8.5px;color:var(--navy)}
.chev{position:absolute;width:5px;height:5px;border-right:1.3px solid var(--navy);border-top:1.3px solid var(--navy);transform:translateY(-50%) rotate(45deg)}
.row-line{position:absolute;left:17px;width:203px;height:1px;background:var(--pale-blue)}
/* stats */
.tab{position:absolute;top:60px;height:20px;border-radius:10px;font-size:8px;font-weight:600;display:flex;align-items:center;justify-content:center;border:1px solid var(--pale-blue);background:#fff;color:var(--navy)}
.tab.active{background:var(--sky);border-color:var(--sky);color:#fff}
.rank-card{position:absolute;top:95px;height:52px;color:#fff;padding:10px 0 0 12px}
.rank-card .small{font-size:8.5px}
.rank-card .big{font-size:12.5px;font-weight:700;margin-top:-1px}
.curve-box{position:absolute;left:23px;top:167px;width:188px;height:149px;border:1px solid var(--soft-blue)}
.box-title{font-size:10.5px;font-weight:600;color:var(--navy)}
.gridline{position:absolute;left:23px;width:188px;height:1px;background:var(--pale-blue)}
.axis-label{font-size:7px;color:#222}
.date{font-size:5.5px;font-weight:600;color:var(--navy)}
.recent-head{position:absolute;left:23px;top:331px;width:188px;height:26px;background:var(--sky);color:#fff;font-size:10px;font-weight:600;padding-left:11px;line-height:26px}
.recent-list{position:absolute;left:23px;top:357px;width:188px;height:80px;border:1px solid var(--soft-blue);border-top:none}
.recent-word{font-size:9.5px;font-weight:600;color:var(--navy)}
</style>
</head>
<body>

<!-- Sign up -->
<section class="screen signup">
  <div class="sky" style="top:0;height:170px" role="img" aria-label="Soft sky with clouds"></div>
  <div class="tc brand" style="left:115px;top:67px">Brivonest</div>
  <div class="tc tagline" style="left:115px;top:92px">Learn letter and words</div>
  <div class="tc heading" style="left:117px;top:196px">Create an account</div>
  <div class="tc subhead" style="left:117px;top:212px">Enter your email to sign up for this app</div>
  <div class="field">email@brivomail.test</div>
  <div class="btn-primary" style="left:26px;top:277px;width:181px;height:30px">Sign up with email</div>
  <div class="rule" style="left:26px;top:327px;width:50px"></div>
  <div class="tc divider-text" style="left:113px;top:327px">or continue with</div>
  <div class="rule" style="left:150px;top:327px;width:50px"></div>
  <div class="alt-login"><span class="dot"></span>Quarnix</div>
  <div class="tc legal" style="left:113px;top:391px">By clicking continue, you agree to our and</div>
  <div class="tc legal-strong" style="left:113px;top:402px">Terms of Service Privacy Policy</div>
</section>

<!-- Main -->
<section class="screen main">
  <header class="topbar">
    <span class="burger"></span>
    <div class="tc screen-title" style="left:115px;top:20px">Main Screen</div>
    <div class="t points" style="left:176px;top:22px">16 Points</div>
  </header>
  <div class="sky" style="top:38px;height:220px"></div>
  <div class="illustration" role="img" aria-label="Two children at an easel covered with scattered letters, holding a giant pencil"></div>
  <div class="toggle"><span class="off">Show all word</span><span class="on">Play all words</span></div>
  <div class="word" style="left:21px;top:296px">Word 1</div>
  <div class="word" style="left:87px;top:296px">Word 2</div>
  <div class="word" style="left:153px;top:296px">Word 3</div>
  <div class="word" style="left:21px;top:322px">Word 4</div>
  <div class="word" style="left:87px;top:322px"></div>
  <div class="btn-primary results">Show me the results</div>
</section>

<!-- Profile -->
<section class="screen profile">
  <header class="topbar">
    <span class="burger"></span>
    <div class="tc screen-title" style="left:117px;top:20px">Profile</div>
  </header>
  <div class="sky" style="top:38px;height:200px"></div>
  <div class="ring" style="left:111px;top:117px;width:94px;height:94px;background:rgba(111,204,234,.18)"></div>
  <div class="ring" style="left:111px;top:117px;width:74px;height:74px;background:rgba(111,204,234,.3)"></div>
  <div class="ring" style="left:111px;top:117px;width:58px;height:58px;background:#fff"></div>
  <div class="ring avatar" style="left:111px;top:117px;width:52px;height:52px" role="img" aria-label="Profile photo of the user"></div>
  <div class="tc" style="left:113px;top:174px;font-size:10px;color:var(--ink)">Edit Profile image</div>

  <div class="t label" style="left:20px;top:221px">Name</div>
  <div class="t value" style="left:83px;top:221px">Mira Dalton</div>
  <span class="chev" style="left:210px;top:221px"></span>
  <div class="row-line" style="top:235px"></div>

  <div class="t label" style="left:20px;top:248px">Username</div>
  <div class="t value" style="left:83px;top:248px">@username</div>
  <span class="chev" style="left:210px;top:248px"></span>
  <div class="row-line" style="top:262px"></div>

  <div class="t label" style="left:20px;top:275px">Email</div>
  <div class="t value" style="left:83px;top:275px">name@brivomail.test</div>
  <span class="chev" style="left:210px;top:275px"></span>
  <div class="row-line" style="top:288px"></div>

  <div class="t label" style="left:20px;top:302px">Links</div>
  <div class="t value" style="left:83px;top:302px">mysite.test</div>
  <div class="t value" style="left:83px;top:319px">ourlink.test</div>
  <div class="t value" style="left:83px;top:337px">yourpage.test</div>
  <div class="t value" style="left:83px;top:355px">Add link</div>
  <div class="row-line" style="top:369px"></div>

  <div class="t label" style="left:20px;top:382px">Bio</div>
  <div class="t value" style="left:82px;top:382px;font-size:7.5px">A description of this user.</div>
  <span class="chev" style="left:210px;top:382px"></span>
</section>

<!-- Stats -->
<section class="screen stats">
  <header class="topbar">
    <span class="burger"></span>
    <div class="tc screen-title" style="left:119px;top:21px">BrivoTally</div>
    <div class="ring avatar" style="left:202px;top:23px;width:18px;height:18px" role="img" aria-label="Small profile photo"></div>
  </header>
  <div class="sky" style="top:38px;height:140px"></div>
  <div class="tab active" style="left:24px;width:63px">Ranking</div>
  <div class="tab" style="left:91px;width:74px">Correct words</div>
  <div class="tab" style="left:169px;width:44px">Todo..</div>
  <div class="rank-card" style="left:27px;width:114px;background:linear-gradient(180deg,var(--blue),var(--navy))">
    <div class="small">Total Ranking</div><div class="big">1st Place of 100</div>
  </div>
  <div class="rank-card" style="left:150px;width:84px;background:linear-gradient(180deg,var(--sky),var(--blue))">
    <div class="small">Daily Ranking</div><div class="big">10th place</div>
  </div>

  <div class="curve-box"></div>
  <div class="t box-title" style="left:35px;top:180px">Learning Curve</div>
  <div class="gridline" style="top:198px"></div>
  <div class="gridline" style="top:217px"></div>
  <div class="gridline" style="top:237px"></div>
  <div class="gridline" style="top:257px"></div>
  <div class="gridline" style="top:276px"></div>
  <div class="gridline" style="top:296px"></div>
  <div class="t axis-label" style="left:35px;top:205px">100 words per day</div>
  <div class="t axis-label" style="left:35px;top:225px">50 words per day</div>
  <div class="t axis-label" style="left:35px;top:245px">.....</div>
  <div class="t axis-label" style="left:35px;top:265px">.....</div>
  <div class="t axis-label" style="left:35px;top:285px">.....</div>
  <svg style="position:absolute;left:23px;top:167px" width="188" height="149" viewBox="0 0 188 149" aria-hidden="true">
    <polyline points="0,128 36,125 59,109 70,114 112,89 120,90 135,71 144,76 154,62 163,66 175,40" fill="none" stroke="#0094D4" stroke-width="1"/>
    <circle cx="175" cy="40" r="4" fill="#6FCCEA" opacity=".6"/>
    <circle cx="175" cy="40" r="2.5" fill="#0677BA"/>
  </svg>
  <div class="t date" style="left:36px;top:304px">Nov 23</div>
  <div class="tc date" style="left:70px;top:304px">24</div>
  <div class="tc date" style="left:91px;top:304px">25</div>
  <div class="tc date" style="left:111px;top:304px">26</div>
  <div class="tc date" style="left:130px;top:304px">27</div>
  <div class="tc date" style="left:149px;top:304px">28</div>
  <div class="tc date" style="left:168px;top:304px">29</div>
  <div class="tc date" style="left:188px;top:304px">30</div>

  <div class="recent-head">Recent learned words</div>
  <div class="recent-list"></div>
  <div class="t recent-word" style="left:36px;top:372px;color:var(--soft-blue)">El</div>
  <div class="gridline" style="top:381px"></div>
  <div class="t recent-word" style="left:36px;top:396px">ELA</div>
  <div class="gridline" style="top:408px"></div>
  <div class="t recent-word" style="left:36px;top:418px">Lorem</div>
</section>

</body>
</html>
```